Stationery Design Project

I need a stationary design for our company. we are based in Houston, TX and we are called Mira Vell Lending. And we are wanting to brand our MoneyMendPlus program, which includes our tax preparation and restoration, credit repair service. Although our business offers other programs, we are interested in mainly focusing on The MoneyMendPlus program. We are looking for way to brand our ourselves and I believe that a great stationery design will help in achieving this goal. Our logo design is blue and light blue. the slogan is orange.

Industry/Entity Type

Business

Requirements
Must have
• Address: 30871 Calloway Ln. B-22
Houston, TX 75419
Tel. 555-318-6207
Fax 555-294-7153
www.miravelllending.example
info@miravelllending.example
Our Slogan: Happiness, Restored!

```html
<!DOCTYPE html>
<html lang="en">
<head>
<meta charset="utf-8">
<title>Mira Vell Lending — Business Card Set</title>
<link rel="stylesheet" href="https://fonts.googleapis.com/css2?family=Jost:wght@400&family=Marcellus+SC&family=Tinos:wght@400&display=swap">
<style>
  :root {
    --stage: #b88a5c;
    --label: #1c140d;
    --card-white: #ffffff;
    --navy: #123f68;
    --brand-blue: #1a5c96;
    --light-blue: #cfe3f3;
    --orange: #f0952c;
    --ink: #2b2b2b;
  }
  * { margin: 0; padding: 0; box-sizing: border-box; }
  html, body { width: 1200px; height: 800px; overflow: hidden; }
  body { background: var(--stage); position: relative; font-family: "Jost", sans-serif; }

  .side-label {
    position: absolute; width: 508px; text-align: center;
    font-family: "Jost", sans-serif; font-size: 22px; color: var(--label);
  }

  .card {
    position: absolute; width: 509px; height: 290px; border-radius: 18px;
    overflow: hidden; box-shadow: 0 4px 12px rgba(0,0,0,.35);
  }
  .card--light { background: var(--card-white); }
  .card--dark { background: var(--navy); }

  .edge-band { position: absolute; right: 0; top: 0; width: 31px; height: 290px; }

  .program-name {
    position: absolute; left: 42px; top: 118px;
    font-family: "Tinos", serif; font-size: 40px; color: var(--brand-blue);
    letter-spacing: -0.5px;
  }
  .program-mark {
    position: absolute; left: 44px; top: 78px; width: 28px; height: 28px;
    background: var(--orange);
  }

  .contact-list {
    position: absolute; left: 45px; top: 197px;
    font-size: 13px; line-height: 16px; color: var(--ink); list-style: none;
  }
  .contact-list b { font-style: italic; font-weight: 400; }
  .contact-divider {
    position: absolute; left: 258px; top: 230px; width: 1px; height: 34px; background: #777;
  }
  .contact-address {
    position: absolute; left: 275px; top: 229px;
    font-size: 13px; line-height: 17px; color: var(--ink); font-style: normal;
  }

  .slogan {
    position: absolute; left: 0; width: 100%; text-align: center;
    font-family: "Marcellus SC", serif; font-size: 20px; color: var(--orange);
    letter-spacing: 0.5px;
  }
  .site-url {
    position: absolute; left: 0; width: 100%; text-align: center;
    font-family: "Jost", sans-serif; font-size: 20px; letter-spacing: 2px;
  }
  .card--light .site-url { color: var(--ink); }
  .card--dark .site-url { color: #ffffff; }

  .name-box {
    position: absolute; background: var(--navy);
    display: flex; align-items: center; justify-content: center;
  }
  .name-box--bordered { outline: 1px solid var(--navy); outline-offset: 3px; }
  .name-box--framed { border: 4px solid var(--light-blue); background: transparent; }
  .company-name {
    font-family: "Tinos", serif; color: #ffffff; font-size: 14px; text-align: center;
  }
  .company-name--large { position: absolute; left: 0; width: 100%; text-align: center; font-size: 21px; }
  .brand-square {
    position: absolute; left: 232px; top: 95px; width: 44px; height: 44px;
    background: var(--light-blue);
  }
</style>
</head>
<body>

  <p class="side-label" style="left:75px; top:50px;">Front</p>
  <p class="side-label" style="left:621px; top:50px;">Back - 1</p>
  <p class="side-label" style="left:75px; top:410px;">Back - 2</p>
  <p class="side-label" style="left:621px; top:410px;">Back - 3</p>

  <!-- Front -->
  <section class="card card--light" style="left:72px; top:90px;">
    <span class="program-mark"></span>
    <p class="program-name">MoneyMendPlus</p>
    <ul class="contact-list">
      <li><b>p</b> : 555-318-6207</li>
      <li><b>f</b> : 555-294-7153</li>
      <li><b>e</b> : info@miravelllending.example</li>
      <li><b>w</b> : www.miravelllending.example</li>
    </ul>
    <span class="contact-divider"></span>
    <address class="contact-address">30871 Calloway Ln. B-22<br>Houston, TX 75419</address>
    <svg class="edge-band" viewBox="0 0 31 290" aria-hidden="true">
      <rect x="0" y="0" width="31" height="290" fill="var(--brand-blue)"/>
      <polygon points="0,0 31,0 31,80 0,110" fill="var(--orange)"/>
    </svg>
  </section>

  <!-- Back 1 -->
  <section class="card card--light" style="left:621px; top:90px;">
    <p class="slogan" style="top:23px;">Happiness, Restored!</p>
    <div class="name-box name-box--bordered" style="left:172px; top:63px; width:164px; height:164px;">
      <p class="company-name">Mira Vell Lending</p>
    </div>
    <p class="site-url" style="top:243px;">www.miravelllending.example</p>
  </section>

  <!-- Back 2 -->
  <section class="card card--dark" style="left:75px; top:450px;">
    <p class="slogan" style="top:21px;">Happiness, Restored!</p>
    <span class="brand-square"></span>
    <p class="company-name company-name--large" style="top:202px;">Mira Vell Lending</p>
    <p class="site-url" style="top:248px;">www.miravelllending.example</p>
  </section>

  <!-- Back 3 -->
  <section class="card card--dark" style="left:621px; top:450px;">
    <p class="slogan" style="top:21px;">Happiness, Restored!</p>
    <div class="name-box name-box--framed" style="left:170px; top:55px; width:169px; height:168px;">
      <p class="company-name">Mira Vell Lending</p>
    </div>
    <p class="site-url" style="top:248px;">www.miravelllending.example</p>
  </section>

</body>
</html>
```